Business Card - high end, modern health care

Hey designers!

We need a double sided business card for the boutique, cutting edge physical therapy rehabilitation centre in Sydney's Northern Beaches.

With the most qualified physios in the area The Harbourview Motion Clinic does what other physiotherapy practices do not, we take our time with our patients giving them longer appointments, better physios and therefor faster results!

We guarantee that the service people receive at THMC will be unparalleled.

Hence we need a business card to reflect our modern, boutique, high end service. The final design needs to reflect that we are in a class of our own yet with the feel of beachside retreat.

Below I have attached our logo in both blue on white and white on blue. The exact colour is;
and the font that we have used in our logo is Tex Gyre Aventador.

I like the idea of the blue as the main colour as it is more eye catching and our signage onto the main road will be in this blue and in the interest of consistency across marketing the blue needs to be a part of the design. However I would appreciate a few designs onto a wooden background as this is a visual theme within the fitout of the practice.

The design needs to be of standard size (91x55mm).

Target Market(s)

We target people who have an end outcome in mind and those who have had poor experiences with other providers and ensure that everyone gets the care that they deserve with a premium service that is tailored to the individuals circumstances. As a premium service, the target market is highly educated, business and tech savvy with the additional target market of elderly people who have self funded their retirement and see value in paying for the best ongoing rehabilitation to maintain independence.

Industry/Entity Type

Physical Therapy

Contact Information for Business Card

Name, designation( Titled Musculoskeletal Physiotherapist... there will also be those in the company that have multiple designations ie 5 or 6 words long), phone number, email, facebook, instagram, address

Font styles to use
Sans Serif

Colors

Designer to choose colors to be used in the design.

Requirements
Must have
• Front - The logo as large as possible, blue or wooden theme, and all of the important details.
• Back - A blank space/lines on which to write appointment times (no "Appointment, date, time" etc.)
Nice to have
• facebook url
• logos for facebook and instagram
• Mini logos for the phone and email?

```html
<!DOCTYPE html>
<html lang="en">
<head>
<meta charset="utf-8">
<title>The Harbourview Motion Clinic – Business Card</title>
<link rel="stylesheet" href="https://fonts.googleapis.com/css2?family=Lato:wght@400;700&display=swap">
<style>
  :root {
    --brand-blue: #0b55a6;
    --card-white: #ffffff;
    --ink: #2a2a2a;
    --page-bg: #eceef1;
  }
  * { margin: 0; padding: 0; box-sizing: border-box; }
  html, body {
    width: 1200px; height: 900px; overflow: hidden;
    background: var(--page-bg);
    font-family: "Lato", sans-serif;
  }
  .business-card {
    position: absolute;
    left: 210px; top: 208px;
    width: 781px; height: 484px;
  }
  .card-shape { position: absolute; inset: 0; }
  .brand-block {
    position: absolute;
    left: 42px; top: 98px; width: 322px;
    display: flex; flex-direction: column; align-items: center;
  }
  .brand-dot {
    width: 190px; height: 190px; border-radius: 50%;
    background: var(--brand-blue);
  }
  .brand-name {
    margin-top: 26px;
    color: var(--brand-blue);
    font-weight: 700; font-size: 23px; line-height: 1.2;
    letter-spacing: 0.5px; text-align: center; text-transform: uppercase;
  }
  .identity, .contact-list {
    position: absolute; right: 48px;
    color: var(--card-white); text-align: right;
  }
  .identity { top: 28px; }
  .person-name { font-weight: 700; font-size: 29px; line-height: 34px; letter-spacing: 0.3px; }
  .person-title { font-size: 22px; line-height: 28px; }
  .contact-row {
    display: flex; justify-content: flex-end; align-items: center;
    gap: 6px; font-size: 21px; line-height: 34px;
  }
  .identity .contact-row { margin-top: 8px; }
  .contact-list { top: 356px; }
  .icon-badge {
    width: 26px; height: 26px; border-radius: 50%;
    background: var(--card-white);
    display: inline-flex; align-items: center; justify-content: center;
    flex: none;
  }
  .icon-badge svg { width: 16px; height: 16px; fill: var(--brand-blue); }
  .appointment-lines {
    position: absolute; right: 48px; top: 200px;
    color: var(--ink); font-size: 19px;
  }
  .write-line {
    display: flex; align-items: flex-end; justify-content: flex-end;
    height: 32px; margin-bottom: 17px;
  }
  .write-line .blank {
    display: inline-block; width: 193px;
    border-bottom: 1.5px solid var(--ink);
    margin-bottom: 4px;
  }
</style>
</head>
<body>
  <div class="business-card">
    <svg class="card-shape" viewBox="0 0 781 484" width="781" height="484" aria-hidden="true">
      <circle cx="241" cy="242" r="241" fill="var(--brand-blue)"/>
      <rect x="241" y="0" width="540" height="484" fill="var(--brand-blue)"/>
      <circle cx="241" cy="242" r="234" fill="var(--card-white)"/>
      <rect x="241" y="156" width="540" height="172" fill="var(--card-white)"/>
    </svg>

    <div class="brand-block">
      <div class="brand-dot"></div>
      <div class="brand-name">The Harbourview<br>Motion Clinic</div>
    </div>

    <div class="identity">
      <div class="person-name">DANIEL WHITFORD</div>
      <div class="person-title">Managing Director</div>
      <div class="contact-row">
        <span>/harbourviewmotionclinic</span>
        <span class="icon-badge"></span>
      </div>
    </div>

    <div class="appointment-lines">
      <div class="write-line"><span class="blank"></span><span>DATE</span></div>
      <div class="write-line"><span class="blank"></span><span>TIME</span></div>
    </div>

    <div class="contact-list">
      <div class="contact-row">
        <span>444 555 0142</span>
        <span class="icon-badge">
          <svg viewBox="0 0 24 24"><path d="M6.6 10.8a15.1 15.1 0 0 0 6.6 6.6l2.2-2.2c.3-.3.7-.4 1-.2 1.1.4 2.3.6 3.6.6.6 0 1 .4 1 1V20c0 .6-.4 1-1 1A17 17 0 0 1 3 4c0-.6.4-1 1-1h3.5c.6 0 1 .4 1 1 0 1.3.2 2.5.6 3.6.1.3 0 .7-.2 1z"/></svg>
        </span>
      </div>
      <div class="contact-row">
        <span>info@harbourviewmotion.com</span>
        <span class="icon-badge">
          <svg viewBox="0 0 24 24"><path d="M3 6h18v12H3z M4.5 7.5 12 13l7.5-5.5" fill="none" stroke="var(--brand-blue)" stroke-width="2"/></svg>
        </span>
      </div>
      <div class="contact-row">
        <span>@harbourviewmotionclinic</span>
        <span class="icon-badge"></span>
      </div>
    </div>
  </div>
</body>
</html>
```